Brindle Recycling needs a new web design

We need a new web design for our company based in Austin, TX. We resell and recycling electronics such as laptops, computer components, Zelvotabs, Quorns, etc. Since our inception over ten years ago, we’ve become one of the premier electronics recycling and remarketing companies in Austin, Texas.

```html
<!DOCTYPE html>
<html lang="en">
<head>
<meta charset="utf-8">
<title>Brindle Recycling</title>
<link href="https://fonts.googleapis.com/css2?family=Montserrat:wght@500;600;700;800&family=Open+Sans:wght@400;600;700&display=swap" rel="stylesheet">
<style>
:root{
  --blue:#1565c0;
  --blue-dark:#0d3f86;
  --blue-bright:#1e88e5;
  --green:#3fae3f;
  --ink:#1d2433;
  --muted:#5b6473;
  --pale-blue:#dcecfb;
  --pale-cyan:#e2f4fb;
  --grey:#f1f2f4;
  --dark:#15181d;
  --white:#ffffff;
  --gold:#f5b50a;
}
*{box-sizing:border-box;margin:0;padding:0}
html,body{width:1200px;height:3156px;overflow:hidden}
body{font-family:"Open Sans",Arial,sans-serif;color:var(--ink);background:var(--white);position:relative}
h1,h2,h3,h4,.nav a,.btn,.brand{font-family:"Montserrat",Arial,sans-serif}
.btn{display:inline-block;font-size:13px;font-weight:600;padding:12px 22px;border-radius:3px;text-decoration:none;color:var(--white);background:var(--blue)}
.btn-outline{background:transparent;border:1px solid var(--white)}
.btn-dark{background:var(--dark)}
p{font-size:13px;line-height:1.65}

/* header */
.site-header{height:72px;display:flex;align-items:center;padding:0 120px;background:var(--white)}
.brand{display:flex;align-items:center;gap:10px;font-size:22px;font-weight:700;color:var(--blue-dark)}
.brand-dot{width:30px;height:30px;border-radius:50%;background:var(--blue)}
.nav{display:flex;margin-left:40px;height:34px;background:var(--blue);border-radius:2px}
.nav a{display:flex;align-items:center;padding:0 16px;color:var(--white);font-size:12px;font-weight:600;text-decoration:none}
.nav a.active{background:var(--blue-dark)}
.header-phone{margin-left:auto;display:flex;align-items:center;gap:8px;font-family:"Montserrat",sans-serif;font-weight:700;font-size:20px;color:var(--blue-dark)}
.header-phone + .btn{margin-left:24px;padding:9px 18px;font-size:12px}

/* hero */
.hero{position:relative;height:608px;overflow:hidden}
.hero-scene{position:absolute;inset:0;background:linear-gradient(180deg,#5fa4da 0%,#a9d1ef 45%,#d8ecf6 60%,#7db24a 66%,#4d8f2a 100%)}
.hero-bin{position:absolute;right:230px;top:40px;width:260px;height:440px;border-radius:40px 40px 70px 70px;background:radial-gradient(circle at 50% 60%,#5fd05a 0 18%,#b9c5cc 19%,#7c8a94 70%,#4f5a62 100%)}
.hero-copy{position:absolute;left:145px;top:180px;width:520px;background:rgba(220,236,250,.85);padding:26px 30px}
.hero-copy h1{font-size:34px;font-weight:700;color:var(--blue-dark);margin-bottom:8px}
.hero-copy p{color:var(--ink);margin-bottom:0}
.hero-actions{position:absolute;left:175px;top:370px;display:flex;gap:18px}
.hero-arrow{position:absolute;top:290px;width:34px;height:34px;border-radius:50%;background:rgba(0,0,0,.45);display:flex;align-items:center;justify-content:center}
.hero-arrow.left{left:78px}.hero-arrow.right{right:78px}

/* about */
.about{display:grid;grid-template-columns:1fr 1fr;height:250px}
.about-col{padding:30px 40px 0 230px}
.about-col + .about-col{padding:30px 230px 0 40px}
.about-col:first-child{background:var(--pale-blue)}
.about-col h2{font-size:21px;font-weight:700;color:var(--blue-dark);margin-bottom:12px}
.about-col p{font-size:12px;margin-bottom:10px;color:var(--muted)}

/* cta */
.cta{height:140px;text-align:center;padding-top:26px}
.cta h2{font-size:25px;font-weight:700;line-height:1.3;margin-bottom:20px}
.cta .btn + .btn{margin-left:14px}

/* service panels */
.services{display:grid;grid-template-columns:1fr 1fr;height:318px}
.service{text-align:center;color:var(--white);padding:60px 110px 0}
.service.recycling{background:linear-gradient(180deg,#1d5aa8,#0e3f7e)}
.service.pickup{background:linear-gradient(180deg,#2b2f36,#101216)}
.service h4{font-size:14px;font-weight:600}
.service h3{font-size:30px;font-weight:700;margin-bottom:14px}
.service p{font-size:12px;margin-bottom:20px;opacity:.9}

/* products */
.products{position:relative;height:490px;background:var(--grey);text-align:center;padding-top:42px}
.products h2{font-size:31px;font-weight:700}
.products h2 span{color:var(--blue-bright)}
.products-bin{position:absolute;left:495px;top:150px;width:210px;height:310px;border-radius:30px 30px 60px 60px;background:radial-gradient(circle at 50% 58%,#5fd05a 0 20%,#b9c5cc 21%,#7c8a94 70%,#4f5a62 100%)}
.product{position:absolute;width:120px;height:120px;border-radius:58% 42% 55% 45%/45% 55% 45% 55%;display:flex;flex-direction:column;align-items:center;justify-content:center;gap:8px;color:var(--white);font-size:12px;font-weight:600}
.product.blue{background:var(--blue-bright)}
.product.black{background:var(--dark)}

/* certified */
.certified{height:590px;background:var(--pale-cyan);text-align:center;padding-top:46px}
.certified h2{font-size:31px;font-weight:700}
.certified h2 span{color:var(--blue-bright)}
.certified .intro{width:720px;margin:14px auto 40px;font-size:12px;color:var(--muted)}
.cert-row{display:flex;justify-content:center;gap:22px}
.cert-card{width:190px;height:300px;background:var(--blue);color:var(--white);padding:44px 22px;text-align:center}
.cert-card p{font-size:12px;margin-bottom:26px}
.cert-card .btn{background:var(--dark);padding:9px 18px;font-size:12px}
.cert-doc{width:190px;height:300px;background:var(--white);border:10px solid #3c8a3c;display:flex;flex-direction:column;align-items:center;padding-top:24px;gap:10px}
.cert-doc.plain{border-color:#d8dde2}
.cert-doc i{display:block;height:5px;background:#c9d1d8;border-radius:2px}
.cert-seal{width:34px;height:34px;border-radius:50%;background:#3c8a3c;margin-top:auto;margin-bottom:24px}

/* testimonials */
.testimonials{position:relative;height:390px;overflow:hidden}
.testimonials-bg{position:absolute;inset:0;background:linear-gradient(90deg,#c7cacf,#e3e5e8 60%,#d6d1c7)}
.testimonials-person{position:absolute;right:0;top:0;width:300px;height:390px;background:linear-gradient(160deg,#e9c58a,#d99a3a 55%,#b9793a)}
.testimonials h2{position:relative;text-align:center;font-size:30px;font-weight:700;padding-top:38px}
.quote-row{position:absolute;left:250px;top:110px;display:flex;width:780px;background:var(--white)}
.quote{flex:1;padding:26px 24px;border-right:1px solid #e3e5e8}
.quote:last-child{border-right:0}
.stars{color:var(--gold);font-size:16px;letter-spacing:2px;margin-bottom:10px}
.quote p{font-size:12px;color:var(--muted);margin-bottom:14px}
.quote h4{font-size:12px;font-weight:700}
.quote-arrow{position:absolute;top:210px;width:26px;height:26px;border-radius:50%;background:var(--blue);display:flex;align-items:center;justify-content:center}

/* footer */
.site-footer{height:296px;background:var(--blue);color:var(--white);position:relative}
.footer-cols{display:flex;padding:36px 0 0 245px;gap:70px}
.footer-col h4{font-size:13px;font-weight:700;margin-bottom:12px}
.footer-col p,.footer-col li{font-size:12px;line-height:1.8;list-style:none;opacity:.9}
.footer-brand{margin-left:30px;padding-top:30px}
.footer-brand .brand{color:var(--white)}
.footer-brand .brand-dot{background:var(--white)}
.socials{display:flex;gap:8px;margin-top:16px;justify-content:flex-end}
.socials span{width:26px;height:26px;background:var(--white);border-radius:3px}
.footer-mark{position:absolute;right:40px;bottom:50px;width:170px;height:170px;border-radius:50%;background:rgba(255,255,255,.08)}
.footer-bottom{position:absolute;left:0;right:0;bottom:0;height:40px;background:var(--blue-dark);font-size:11px;padding:12px 245px}
.contact-tab{position:absolute;right:30px;bottom:8px;background:var(--white);color:var(--blue-dark);font-size:11px;font-weight:700;padding:6px 14px;border-radius:2px}
</style>
</head>
<body>

<header class="site-header">
  <div class="brand"><span class="brand-dot"></span>Brindle Recycling</div>
  <nav class="nav">
    <a class="active" href="#">HOME</a><a href="#">ABOUT</a><a href="#">SERVICES</a><a href="#">CERTIFICATIONS</a><a href="#">NEWS</a><a href="#">CONTACT</a>
  </nav>
  <div class="header-phone">
    <svg width="18" height="18" viewBox="0 0 24 24"><path fill="#0d3f86" d="M6.6 10.8a15 15 0 0 0 6.6 6.6l2.2-2.2c.3-.3.7-.4 1-.2 1.1.4 2.3.6 3.6.6.6 0 1 .4 1 1V20c0 .6-.4 1-1 1A17 17 0 0 1 3 4c0-.6.4-1 1-1h3.5c.6 0 1 .4 1 1 0 1.3.2 2.5.6 3.6.1.3 0 .7-.2 1z"/></svg>
    (512) 555-0147
  </div>
  <a class="btn" href="#">Book online</a>
</header>

<section class="hero">
  <div class="hero-scene" role="img" aria-label="Blue sky over a green grass field"></div>
  <div class="hero-bin" role="img" aria-label="Recycling bin full of old computers and electronics"></div>
  <div class="hero-copy">
    <h1>Recycling Today Reuse Tomorrow</h1>
    <p>We resell and recycle electronics such as laptops, computer components, Zelvotabs, Quorns, etc.</p>
  </div>
  <div class="hero-actions">
    <a class="btn" href="#">Schedule A Pickup</a>
    <a class="btn btn-dark" href="#">Call (512) 555-0147</a>
  </div>
  <span class="hero-arrow left"><svg width="12" height="12" viewBox="0 0 12 12"><path d="M8 1 3 6l5 5" stroke="#fff" stroke-width="2" fill="none"/></svg></span>
  <span class="hero-arrow right"><svg width="12" height="12" viewBox="0 0 12 12"><path d="m4 1 5 5-5 5" stroke="#fff" stroke-width="2" fill="none"/></svg></span>
</section>

<section class="about">
  <div class="about-col">
    <h2>About Brindle Recycling</h2>
    <p>At Brindle Recycling, we're committed to providing environmentally friendly recycling solutions to Austin and the surrounding areas.</p>
    <p>Founded in 2008, our mission is to provide you with the best service at a fair price, with a focus on your security and satisfaction. As a recycling center, we resell, reuse and recycle responsibly.</p>
  </div>
  <div class="about-col">
    <h2>Computer Recycling Made Easy</h2>
    <p>We're to make a difference in our environment and planet! Brindle Recycling is here to help! Since inception, our team has been helping keep the environment healthy since 2008.</p>
    <p>We specialize in recycling services that help protect the planet, such as recycling waste. We have a passion to keep our community safe and clean through the proper reuse of old equipment.</p>
  </div>
</section>

<section class="cta">
  <h2>Do you have any computer or electronic<br>equipment to recycling of?</h2>
  <a class="btn" href="#">Schedule A Pickup</a><a class="btn btn-dark" href="#">Call (512) 555-0147</a>
</section>

<section class="services">
  <div class="service recycling">
    <h4>Environmentally Friendly</h4>
    <h3>Electronic Recycling</h3>
    <p>At Brindle Recycling, we strive to keep the environment clean through our wide range of services. Our Electronic Recycling process was designed to simplify the recycling process for residents and businesses alike, and we make sure your items are handled safely.</p>
    <a class="btn btn-outline" href="#">Schedule A Pickup</a>
  </div>
  <div class="service pickup">
    <h4>We Come To You</h4>
    <h3>Recycling Pickup</h3>
    <p>At Brindle Recycling, we go out of our way to make recycling convenient. Our Recycling Pickup service is designed to simplify your recycling. Take a look at the services we offer and we'll come to you to collect your old electronics.</p>
    <a class="btn btn-outline" href="#">Schedule A Pickup</a>
  </div>
</section>

<section class="products">
  <h2><span>Recycling</span> Products</h2>
  <div class="products-bin" role="img" aria-label="Recycling bin full of electronics"></div>
  <div class="product blue" style="left:215px;top:165px">
    <svg width="40" height="32" viewBox="0 0 40 32"><rect x="2" y="2" width="36" height="22" rx="2" fill="none" stroke="#fff" stroke-width="3"/><path d="M14 30h12M20 24v6" stroke="#fff" stroke-width="3"/></svg>Computers</div>
  <div class="product black" style="left:320px;top:265px">
    <svg width="40" height="30" viewBox="0 0 40 30"><rect x="6" y="3" width="28" height="18" rx="2" fill="none" stroke="#fff" stroke-width="3"/><path d="M2 26h36" stroke="#fff" stroke-width="3"/></svg>Laptops</div>
  <div class="product black" style="left:265px;top:370px">
    <svg width="40" height="30" viewBox="0 0 40 30"><rect x="2" y="4" width="36" height="20" rx="2" fill="none" stroke="#fff" stroke-width="3"/><path d="M12 28h16" stroke="#fff" stroke-width="3"/></svg>TVs</div>
  <div class="product black" style="left:760px;top:165px">
    <svg width="40" height="32" viewBox="0 0 40 32"><rect x="4" y="2" width="32" height="22" rx="3" fill="none" stroke="#fff" stroke-width="3"/><path d="M16 30h8" stroke="#fff" stroke-width="3"/></svg>Quorns</div>
  <div class="product blue" style="left:865px;top:265px">
    <svg width="36" height="36" viewBox="0 0 36 36"><rect x="8" y="8" width="20" height="20" fill="none" stroke="#fff" stroke-width="3"/><path d="M13 2v6M23 2v6M13 28v6M23 28v6M2 13h6M2 23h6M28 13h6M28 23h6" stroke="#fff" stroke-width="2.5"/></svg>Components</div>
  <div class="product blue" style="left:810px;top:370px">
    <svg width="28" height="36" viewBox="0 0 28 36"><rect x="2" y="2" width="24" height="32" rx="3" fill="none" stroke="#fff" stroke-width="3"/><circle cx="14" cy="29" r="1.8" fill="#fff"/></svg>Zelvotabs</div>
</section>

<section class="certified">
  <h2><span>Certified</span> Recyclers</h2>
  <p class="intro">The recycling of electronic waste protects the environment, conserves raw materials and reduces landfill use. Our certified process ensures your equipment is handled responsibly and your data remains secure.</p>
  <div class="cert-row">
    <div class="cert-card">
      <p>Brindle Recycling has been certified by a leading standards body for its Environmental Management System and its commitment to responsible electronics recycling in Austin.</p>
      <a class="btn" href="#">Full View</a>
    </div>
    <div class="cert-doc"><i style="width:110px"></i><i style="width:80px"></i><i style="width:130px"></i><i style="width:120px"></i><i style="width:90px"></i><span class="cert-seal"></span></div>
    <div class="cert-doc"><i style="width:110px"></i><i style="width:80px"></i><i style="width:130px"></i><i style="width:120px"></i><i style="width:90px"></i><span class="cert-seal"></span></div>
    <div class="cert-doc plain"><i style="width:110px"></i><i style="width:80px"></i><i style="width:130px"></i><i style="width:120px"></i><i style="width:90px"></i><span class="cert-seal" style="background:#1565c0"></span></div>
  </div>
</section>

<section class="testimonials">
  <div class="testimonials-bg" role="img" aria-label="Soft grey office backdrop"></div>
  <div class="testimonials-person" role="img" aria-label="Smiling customer in a yellow top"></div>
  <h2>Testimonials</h2>
  <div class="quote-row">
    <div class="quote"><div class="stars">★★★★★</div><p>Booking a pickup was simple and the team arrived right on time. They took every old laptop and monitor we had and handled everything with real care. Highly recommend them.</p><h4>MARLA T.</h4></div>
    <div class="quote"><div class="stars">★★★★★</div><p>Friendly staff, fair prices and a clear process from start to finish. Our office finally cleared out years of old computer parts without any hassle at all.</p><h4>DEVON S.</h4></div>
    <div class="quote"><div class="stars">★★★★★</div><p>I felt confident knowing my data was wiped securely. The crew was quick, polite and explained exactly how each device would be reused or recycled.</p><h4>JORIE K.</h4></div>
  </div>
  <span class="quote-arrow" style="left:218px"><svg width="10" height="10" viewBox="0 0 12 12"><path d="M8 1 3 6l5 5" stroke="#fff" stroke-width="2" fill="none"/></svg></span>
  <span class="quote-arrow" style="left:1044px"><svg width="10" height="10" viewBox="0 0 12 12"><path d="m4 1 5 5-5 5" stroke="#fff" stroke-width="2" fill="none"/></svg></span>
</section>

<footer class="site-footer">
  <span class="footer-mark"></span>
  <div class="footer-cols">
    <div class="footer-col">
      <h4>CONTACT INFO</h4>
      <p>4820 Harlow Bend<br>Austin, TX 78741<br><br>(512) 555-0147<br>hello@brindlerecycling.com</p>
    </div>
    <div class="footer-col">
      <h4>QUICK LINKS</h4>
      <ul><li>Home</li><li>About</li><li>Services</li><li>Certifications</li><li>News</li><li>Contact</li></ul>
    </div>
    <div class="footer-col">
      <h4>HELPFUL LINKS</h4>
      <ul><li>Service Area</li><li>Rates</li><li>Terms of Use</li><li>Privacy Policy</li><li>Sitemap</li></ul>
    </div>
    <div class="footer-brand">
      <div class="brand"><span class="brand-dot"></span>Brindle Recycling</div>
      <div class="socials"><span></span><span></span><span></span></div>
    </div>
  </div>
  <div class="footer-bottom">© 2024 Brindle Recycling. All Rights Reserved.</div>
  <span class="contact-tab">CONTACT US</span>
</footer>

</body>
</html>
```